A5 Patient Information Booklet (Chiropractic Clinic) 4-8 pages

Here’s a polished, professional rewrite of your full brief and content, with clearer structure, corrected language, and a premium tone:

---

**Project Title:** Premium Patient Information Brochure (Chiropractic & Wellness Clinic)

---

### **Overview**

We are a health and wellness clinic seeking a premium, high-end patient information brochure to provide following a patient’s initial consultation and first treatment.

The purpose of this booklet is to:

* Reinforce trust and professionalism
* Help patients understand what to expect next
* Encourage adherence to care recommendations
* Position the clinic as calm, expert-led, and results-driven

---

### **Format**

* 4–8 page booklet (A5 or similar size)
* Print-ready and digital versions required

---

### **Target Audience**

Patients who have just completed their initial consultation and may have begun treatment. They may already be experiencing physical or mental changes, so the brochure should guide, reassure, and educate them on what comes next.

---

### **Tone & Style**

* Premium, calm, and reassuring
* Modern wellness aesthetic (not overly clinical)
* Clean layout with minimal clutter
* Soft, neutral colour palette (whites, creams, muted greens, soft blues)
* Elegant typography (e.g. Montserrat / Lato)
* High-end, trustworthy, and professional feel

---

### **Key Messages**

#### 1. Listen to Your Body

Patients may feel different after treatment. Reassure them that this is normal and part of the healing process.

#### 2. Post-Treatment Advice

* Stay well hydrated
* Rest if needed
* Avoid overexertion if the body requires recovery

#### 3. Healing is a Journey (Core Concept)

A strong visual metaphor of a **“road to recovery”** or **journey** should be central to the design.

This journey should clearly illustrate three phases:

* **Phase 1: Initial Care (Weeks 1–6)**
Focus: Reducing pain/discomfort, calming the body, and initiating response to treatment

* **Phase 2: Corrective Care (Weeks 6–12)**
Focus: Addressing underlying issues, improving function, and creating lasting change

* **Phase 3: Wellness / Maintenance (Ongoing)**
Focus: Maintaining progress, preventing relapse, and supporting long-term wellbeing

**Important:**

* Emphasise that this is not a quick fix
* Progress requires time and consistency
* Each patient follows an individualised care plan
* The journey should feel structured, positive, and achievable

#### 4. Personalised Care

Reinforce that every treatment plan is tailored specifically to the individual.

#### 5. Professional Reassurance

Patients should feel confident they are in expert hands and supported throughout their journey.

---

### **Design Direction**

* Use imagery that reflects calmness, progression, and wellness (e.g. pathways, nature, soft gradients)
* Avoid generic stock imagery
* **Only use original clinic images from website and social media**
* Prioritise white space and clarity
* Aim for a luxury spa/medical hybrid aesthetic

---

## **Content Structure (Page-by-Page)**

### **Front Cover**

* Clean, minimal, premium design
* Clinic branding

---

### **Page 1: Patient Case Summary**

**Title:** *Welcome to Fernwell Spine Studio*

Thank you for choosing Fernwell Spine Studio.

This booklet is designed to guide you through:

* What we found during your initial consultation
* Your personalised recommended treatment plan
* Your road to recovery
* Long-term wellness care
* Why we take the approach we do

---

### **Page 2: Your Care Journey**

**Stage 1: Your Initial Consultation**

Today we completed a comprehensive assessment of your health and function, including:

* Full case history and discussion of your symptoms and goals
* Orthopaedic and neurological testing
* Postural and movement assessment
* Initial treatment (where appropriate)

**What this tells us:**

* How your body is currently functioning
* Where areas of stress or dysfunction may be present
* The most appropriate and effective path forward for your care

---

### **Page 3: Your Suggested Treatment Plan**

Based on today’s findings, your recommended care plan is:

**______ treatments over ______ weeks**

This should be viewed alongside your *Road to Recovery* to help you understand what to expect.

We have also discussed:

* Expected timelines for improvement
* Available payment options

**After Treatment:**
It is common to feel different following treatment. This is a normal response as your body begins to adapt and respond.

We recommend:

* Staying well hydrated
* Allowing time for rest and recovery
* Avoiding overexertion if your body feels it needs it

---

### **Page 4: What to Expect Next**

Healing is not always linear—it is a process that occurs over time.

Your care will typically progress through the following stages:

* **Relief Care**
Focused on reducing discomfort and calming the body

* **Corrective Care**
Focused on addressing underlying issues and improving function
(This phase may include prescribed exercises)

* **Maintenance / Wellness Care**
Focused on sustaining progress, preventing recurrence, and supporting long-term health

---

### **Page 5: Understanding Chiropractic Care**

**What is Chiropractic?**
Chiropractic care focuses on the relationship between the spine, nervous system, and overall body function.

By improving spinal movement and alignment, chiropractic care helps support the nervous system, allowing the body to function and heal more effectively.

**About Fernwell Spine Studio**
At Fernwell Spine Studio, our approach is centred around personalised, patient-focused care. We aim to not only relieve symptoms but to address underlying causes and support long-term wellbeing.

---

### **Back Page**

* Clinic contact details
* Website
* Social media icons/handles

**Closing Message:**
“A healthier, stronger you—supported every step of the way.”

---

### **Deliverables**

* Print-ready PDF
* Editable source files

---

### **Additional Notes**

* The brochure should feel valuable and worth keeping
* Encourage long-term care in a subtle, non-pushy way
* Maintain clarity, readability, and strong visual hierarchy
* Balance professionalism with warmth and approachability

---

If you’d like, I can also turn this into **actual brochure copy (fully written, patient-facing text)** or help you refine it further for a designer.

Existing patients who want to feel better and look after themselves that is given after their initil consultation appointment

Chiropractic, wellness, health

• Montserrat or Lato

0094D4
00A9DD
6FCCEA
C7EBF8
E9F6FB
00AB8E
00BBA5
67D7C9
C6EFE9
E9F9F6
6B429C
8869AF
B7A5CE
E3DAEB
F3F0F8

• my own photos, look premium wellness, be clear and simple to understand for patients journey or what to expect next and over time
• USe my social media/website for ideas
• generic photos and images

```html
<!DOCTYPE html>
<html lang="en">
<head>
<meta charset="utf-8">
<title>Fernwell Spine Studio – Patient Care Booklet</title>
<link href="https://fonts.googleapis.com/css2?family=Lato:wght@400;700;900&display=swap" rel="stylesheet">
<style>
:root{
  --backdrop:#3a3839;
  --teal:#17a49b;
  --teal-dark:#12908a;
  --pink:#e9579e;
  --pink-soft:#f37fb6;
  --purple:#a98bd2;
  --blue:#62ace2;
  --ink:#3c3f44;
  --muted:#5f6368;
  --white:#ffffff;
}
*{margin:0;padding:0;box-sizing:border-box}
html,body{width:1200px;height:2198px;overflow:hidden}
body{background:var(--backdrop);font-family:'Lato',sans-serif;color:var(--ink);position:relative}
.page{position:absolute;width:476px;height:618px;background:var(--white);overflow:hidden}
.page--cover{left:87px;top:97px}
.page--aftercare{left:636px;top:97px}
.page--about{left:87px;top:790px}
.page--journey{left:636px;top:790px}
.page--road{left:87px;top:1483px}
.abs{position:absolute}
.photo{position:absolute;left:0;top:0}
.heading{position:absolute;color:var(--teal);font-weight:900;font-size:13.5px;letter-spacing:.1px;line-height:1.12}
.copy{position:absolute;font-size:9.6px;line-height:16.4px;color:var(--muted);text-align:justify}
.copy--tight{line-height:14px}
.copy--line{white-space:nowrap;text-align:left;line-height:14px}
.copy strong{color:var(--ink);font-weight:700}

/* cover */
.brand-panel{position:absolute;right:0;top:0;width:172px;height:212px;background:var(--white);text-align:center}
.brand-dot{width:64px;height:64px;border-radius:50%;border:3px solid var(--teal);margin:22px auto 12px}
.brand-name{font-size:14px;font-weight:700;color:#2c3338;line-height:1.2;padding:0 10px}
.cover-title{position:absolute;left:0;width:476px;top:452px;text-align:center;color:var(--white);font-weight:900;font-size:25px;line-height:27px}
.cover-intro{position:absolute;left:50px;width:376px;top:512px;text-align:center;color:var(--white);font-size:9.2px;line-height:14.5px}
.cover-field{position:absolute;color:var(--white);font-size:9px;white-space:nowrap}

/* cards */
.tip{position:absolute;width:203px;height:53px;background:var(--white);border-radius:27px;box-shadow:0 2px 8px rgba(60,60,80,.14);padding:8px 10px 0 42px}
.tip-icon{position:absolute;left:8px;top:11px;width:30px;height:30px;border-radius:50%;background:var(--pink-soft);border:3px solid #fbd3e6}
.tip-title{color:var(--pink);font-weight:700;font-size:8.8px;margin-bottom:2px}
.tip-text{font-size:7.6px;line-height:11.5px;color:var(--muted)}

/* footer band */
.footer-band{position:absolute;left:0;bottom:0;width:476px;height:100px}
.footer-text{position:absolute;left:0;width:476px;bottom:8px;text-align:center;color:var(--white)}
.footer-text b{display:block;font-weight:900;font-size:11px;line-height:13px}
.footer-text span{display:block;font-size:8.2px;margin-top:3px}

/* lists */
.ticks{position:absolute;list-style:none;font-size:9.2px;color:var(--muted)}
.ticks li{position:relative;padding-left:17px;height:16px;white-space:nowrap}
.ticks li::before{content:"";position:absolute;left:0;top:2px;width:9px;height:9px;border-radius:50%;background:var(--pink-soft)}
.ticks li::after{content:"";position:absolute;left:3px;top:4px;width:3px;height:4px;border:solid #fff;border-width:0 1.2px 1.2px 0;transform:rotate(45deg)}

/* journey pill */
.journey-pill{position:absolute;left:-40px;top:172px;width:556px;height:204px;border-radius:110px;background:linear-gradient(90deg,var(--pink-soft),var(--purple) 50%,var(--blue))}
.journey-title{position:absolute;left:0;width:476px;top:198px;text-align:center;color:var(--white);font-weight:900;font-size:14px}
.journey-sub{position:absolute;left:0;width:476px;top:216px;text-align:center;color:var(--white);font-size:7.8px}
.phase{position:absolute;top:242px;width:110px;text-align:center;color:var(--white)}
.phase-icon{width:36px;height:36px;border-radius:50%;background:var(--white);margin:0 auto 6px;border:3px solid rgba(255,255,255,.6);box-shadow:inset 0 0 0 7px #f7d4e6}
.phase-name{font-size:8.6px;margin-bottom:5px}
.phase-pill{display:inline-block;background:var(--teal);border-radius:9px;font-size:7.6px;font-weight:700;padding:3px 12px;margin-bottom:4px}
.phase-text{font-size:7px;line-height:10.5px;opacity:.95}

/* road chart */
.road-card{position:absolute;left:72px;top:213px;width:336px;height:194px;background:var(--white);border-radius:12px;box-shadow:0 3px 12px rgba(0,0,0,.18);overflow:hidden}
.road-band{position:absolute;left:0;top:0;width:34px;height:194px;background:var(--teal);border-radius:12px 0 0 12px}
.road-band span{position:absolute;left:17px;top:97px;transform:translate(-50%,-50%) rotate(-90deg);white-space:nowrap;color:var(--white);font-weight:900;font-size:14px}
.road-levels{position:absolute;left:36px;top:6px;width:50px;list-style:none;text-align:right}
.road-levels li{font-size:4.6px;font-weight:900;color:#555;height:20px;border-bottom:.6px solid #ccc;padding-top:6px}
.road-scale{position:absolute;left:88px;top:4px;width:6px;height:186px;background:linear-gradient(#2bb08e,#a9cf3a,#f2c223,#e8592b,#c92a2a)}
.road-graph{position:absolute;left:98px;top:4px;width:232px;height:186px;background:linear-gradient(160deg,#eef5fb 0%,#dbeedf 35%,#f5e6b9 60%,#f0c3b0 85%,#e5a3a3 100%);border-radius:4px}
.road-text{position:absolute;left:40px;width:396px;top:428px;text-align:center;font-size:9.6px;line-height:17.5px;color:var(--muted)}
.road-tagline{position:absolute;left:0;width:476px;top:500px;text-align:center;color:var(--teal);font-size:9.8px;font-weight:700}
</style>
</head>
<body>

<svg width="0" height="0" style="position:absolute">
  <defs>
    <linearGradient id="arcStroke" x1="0" x2="1" y1="0" y2="0">
      <stop offset="0" stop-color="#e47ab8"/>
      <stop offset=".5" stop-color="#b495d6"/>
      <stop offset="1" stop-color="#6aa9e3"/>
    </linearGradient>
    <symbol id="footerBand" viewBox="0 0 476 100">
      <path d="M34,100 Q238,-30 442,100 Z" fill="url(#arcStroke)"/>
      <path d="M46,100 Q238,-16 430,100 Z" fill="#17a49b"/>
      <circle cx="238" cy="36" r="15" fill="#fff"/>
      <path d="M231,30 h14 a3,3 0 0 1 3,3 v6 a3,3 0 0 1 -3,3 h-8 l-4,4 v-4 h-2 a3,3 0 0 1 -3,-3 v-6 a3,3 0 0 1 3,-3z" fill="#17a49b"/>
      <circle cx="234.5" cy="36" r="1" fill="#fff"/><circle cx="238" cy="36" r="1" fill="#fff"/><circle cx="241.5" cy="36" r="1" fill="#fff"/>
    </symbol>
  </defs>
</svg>

<!-- Cover -->
<section class="page page--cover">
  <div class="photo" role="img" aria-label="Photo of a chiropractor showing a spine model to a patient holding her lower back" style="width:476px;height:520px;background:linear-gradient(120deg,#eae7e3 0%,#d8d2cc 40%,#c7d2dc 75%,#e9edf0 100%)"></div>
  <div class="brand-panel">
    <div class="brand-dot"></div>
    <div class="brand-name">Fernwell Spine Studio</div>
  </div>
  <svg class="abs" style="left:0;top:0" width="476" height="618" viewBox="0 0 476 618">
    <path d="M0,512 Q238,286 476,512 L476,618 L0,618Z" fill="url(#arcStroke)"/>
    <path d="M0,522 Q238,300 476,522 L476,618 L0,618Z" fill="#17a49b"/>
    <circle cx="238" cy="402" r="46" fill="#fff"/>
    <circle cx="238" cy="402" r="38" fill="none" stroke="#17a49b" stroke-width="3"/>
  </svg>
  <h1 class="cover-title">YOUR PERSONAL CARE<br>JOURNEY</h1>
  <p class="cover-intro">This booklet is designed to guide you through your care, help you understand your body, and support you in achieving long-term health and wellbeing.</p>
  <div class="cover-field" style="left:80px;top:548px">Patient Name: &nbsp;&nbsp;&nbsp;------------------------------ &nbsp;&nbsp;&nbsp;&nbsp;&nbsp;&nbsp;Date: &nbsp;&nbsp;&nbsp;------------------------------</div>
  <div class="cover-field" style="left:94px;top:572px">------------------------------ &nbsp;treatments. Over: ------------------------ &nbsp;&nbsp;weeks</div>
  <div class="cover-field" style="left:143px;top:595px">Review/Reassessment at: &nbsp;&nbsp;&nbsp;------------------------</div>
</section>

<!-- Aftercare -->
<section class="page page--aftercare">
  <svg class="abs" style="left:0;top:0" width="476" height="270" viewBox="0 0 476 270">
    <path d="M0,176 Q238,340 476,176" fill="none" stroke="url(#arcStroke)" stroke-width="9"/>
    <path d="M0,0 H476 V172 Q238,332 0,172Z" fill="#8a8d92" role="img" aria-label="Photo of a chiropractor adjusting a patient lying on a treatment table"/>
  </svg>
  <h2 class="heading" style="left:26px;top:298px">YOU ARE IN GOOD HANDS</h2>
  <p class="copy copy--tight" style="left:26px;top:317px;width:202px">We take a thorough, personalised approach because lasting results come from understanding the real cause of your problem.</p>
  <p class="copy copy--tight" style="left:26px;top:374px;width:202px">We are here to guide and support you every step of the way.</p>
  <h2 class="heading" style="left:26px;top:416px;width:200px">WHAT TO EXPECT AFTER YOUR TREATMENT</h2>
  <div class="tip" style="left:247px;top:305px"><span class="tip-icon"></span><div class="tip-title">LISTEN TO YOUR BODY</div><div class="tip-text">You may feel relief, mild soreness, or movement changes - this is normal.</div></div>
  <div class="tip" style="left:247px;top:381px"><span class="tip-icon"></span><div class="tip-title">REST WHEN NEEDED</div><div class="tip-text">Give your body time to rest - avoid overexertion.</div></div>
  <div class="tip" style="left:26px;top:456px"><span class="tip-icon"></span><div class="tip-title">STAY HYDRATED</div><div class="tip-text">Drinking plenty of water supports your body's natural recovery process.</div></div>
  <div class="tip" style="left:247px;top:456px"><span class="tip-icon"></span><div class="tip-title">TRUST THE PROCESS</div><div class="tip-text">Lasting change takes time - focus on long-term results, not quick relief.</div></div>
  <svg class="footer-band"><use href="#footerBand"/></svg>
  <div class="footer-text"><b>WE ENCOURAGE</b><b>YOU TO ASK QUESTIONS AT ANY TIME.</b><span>Understanding your care builds confidence - and better results.</span></div>
</section>

<!-- About -->
<section class="page page--about">
  <svg class="abs" style="left:0;top:0" width="476" height="250" viewBox="0 0 476 250">
    <path d="M0,134 Q238,336 476,134" fill="none" stroke="url(#arcStroke)" stroke-width="9"/>
    <path d="M0,0 H476 V130 Q238,326 0,130Z" fill="#a9aeb1" role="img" aria-label="Photo of a chiropractor explaining a spine model to a seated patient"/>
  </svg>
  <h2 class="heading" style="left:26px;top:256px">WHAT IS CHIROPRACTIC CARE?</h2>
  <p class="copy" style="left:26px;top:274px;width:200px;text-align:left"><strong>Chiropractic care focuses on how your body moves, functions, and heals as a whole.</strong></p>
  <p class="copy" style="left:26px;top:322px;width:200px">By improving the alignment and mobility of the spine and joints, it helps reduce pressure on the nervous system, allowing your body to function more efficiently. Rather than simply masking symptoms, this approach supports your body's natural ability to adapt, recover, and maintain long-term health.</p>
  <h2 class="heading" style="left:26px;top:452px">YOUR CHIROPRACTOR</h2>
  <p class="copy" style="left:26px;top:470px;width:200px">At Fernwell Spine Studio, your care is led by chiropractor Maren, who takes a personalised, hands-on approach to your health.</p>
  <p class="copy" style="left:250px;top:254px;width:200px">Every consultation is focused on understanding your body, your lifestyle, and your goals—so your treatment plan is tailored specifically to you. Maren combines clinical expertise with a calm, supportive environment to help you feel confident, informed, and in control of your recovery journey.</p>
  <h2 class="heading" style="left:250px;top:383px">ABOUT FERNWELL SPINE STUDIO</h2>
  <p class="copy" style="left:250px;top:401px;width:200px">At Fernwell Spine Studio, we believe that true health is built over time—not achieved through quick fixes. Our approach is centred around personalised care, attention to detail, and long-term results. We work with you to not only relieve symptoms, but to improve how your body functions and performs in everyday life.</p>
  <svg class="footer-band"><use href="#footerBand"/></svg>
  <div class="footer-text"><b>WE ENCOURAGE</b><b>YOU TO ASK QUESTIONS AT ANY TIME.</b><span>Understanding your care builds confidence - and better results.</span></div>
</section>

<!-- Journey -->
<section class="page page--journey">
  <h2 class="heading" style="left:34px;top:24px;font-size:11.5px">WHY CONTINUING CARE MATTERS</h2>
  <p class="copy copy--tight" style="left:34px;top:41px;width:188px">Pain often improves before the body is fully healed.</p>
  <p class="copy copy--line" style="left:34px;top:72px"><strong>Stopping care too early can lead to:</strong></p>
  <ul class="ticks" style="left:44px;top:89px"><li>Symptoms returning</li><li>Incomplete healing</li><li>Ongoing underlying problems</li></ul>
  <p class="copy copy--line" style="left:34px;top:140px">Consistency is what creates lasting results.</p>
  <h2 class="heading" style="left:256px;top:24px;font-size:11.5px">YOUR ROLE IN YOUR RESULTS</h2>
  <p class="copy copy--line" style="left:256px;top:41px">The best outcomes come from working together.</p>
  <p class="copy copy--line" style="left:256px;top:57px"><strong>To get the most from your care:</strong></p>
  <ul class="ticks" style="left:266px;top:81px"><li>Attend your scheduled appointments</li><li>Follow your exercises and advice</li><li>Stay consistent with your plan</li><li>Let us know how you're progressing</li></ul>
  <div class="photo" role="img" aria-label="Photo of a practitioner's hands on a spine model beside a patient" style="top:330px;width:476px;height:288px;background:linear-gradient(135deg,#d9dadd,#b9b4ad 50%,#8b93a3)"></div>
  <div class="journey-pill"></div>
  <h2 class="journey-title">YOUR RECOMMENDED CARE JOURNEY</h2>
  <p class="journey-sub">Your care is structured in phases to give you the best long-term results.</p>
  <div class="phase" style="left:61px"><div class="phase-icon"></div><div class="phase-name">Phase 1: Relief</div><span class="phase-pill">Short-term focus</span><div class="phase-text">Sed ut perspiciatis unde omnis iste natus error sit voluptatem accusan tium dolorem</div></div>
  <div class="phase" style="left:183px"><div class="phase-icon"></div><div class="phase-name">Phase 2: Restore</div><span class="phase-pill">Mid-term focus</span><div class="phase-text">Sed ut perspiciatis unde omnis iste natus error sit voluptatem accusan tium dolorem</div></div>
  <div class="phase" style="left:305px"><div class="phase-icon"></div><div class="phase-name">Phase 3: Thrive</div><span class="phase-pill">Long-term focus</span><div class="phase-text">Sed ut perspiciatis unde omnis iste natus error sit voluptatem accusan tium dolorem</div></div>
  <svg class="footer-band"><use href="#footerBand"/></svg>
  <div class="footer-text"><b>WE ENCOURAGE</b><b>YOU TO ASK QUESTIONS AT ANY TIME.</b><span>Understanding your care builds confidence - and better results.</span></div>
</section>

<!-- Road to recovery -->
<section class="page page--road">
  <svg class="abs" style="left:0;top:0" width="476" height="280" viewBox="0 0 476 280">
    <path d="M0,198 Q238,334 476,198" fill="none" stroke="url(#arcStroke)" stroke-width="9"/>
    <path d="M0,0 H476 V194 Q238,326 0,194Z" fill="#c9c6c2" role="img" aria-label="Photo of a chiropractor holding a spine model while a patient listens"/>
  </svg>
  <div class="road-card">
    <div class="road-band"><span>ROAD TO RECOVER</span></div>
    <ul class="road-levels"><li>OPTIMISING</li><li>ENHANCING</li><li>CORRECTING</li><li>STABILISING</li><li>STRENGTHENING</li><li>HEALING</li><li>RECOVERING</li><li>IMPROVING</li><li>SUFFERING</li></ul>
    <div class="road-scale"></div>
    <div class="road-graph" role="img" aria-label="Illustrated recovery road winding upward from the pain line through healing, correction and maintenance phases over days, weeks, months and years"></div>
  </div>
  <p class="road-text">At Fernwell Spine Studio Chiropractic &amp; Wellness Ashby, we offer personalised chiropractic care for adults and families who want to feel their best — whether that's easing discomfort, improving movement, or supporting long-term wellbeing.</p>
  <p class="road-tagline">Align your body, elevate your wellbeing</p>
  <svg class="footer-band"><use href="#footerBand"/></svg>
  <div class="footer-text"><b>WE ENCOURAGE</b><b>YOU TO ASK QUESTIONS AT ANY TIME.</b><span>Understanding your care builds confidence - and better results.</span></div>
</section>

</body>
</html>
```